Dew and Willow med spa needs an awesome eye catching billboard ad

We need a billboard ad design for a Med Spa with location sin Davenport and Windermere FL A medical spa where the beauty of nature meets the power of science to treat the whole person, mind, body and soul.

Marigold Radiance Med Spa is a medical spa where the beauty of nature meets the power of science to create gorgeous, youthful looking skin. Located in Davenport, Florida, but also serving Four Corners, Celebration, and Windermere, Florida, the talented professional team brings decades of experience in world-class skin care to provide holistic, science-backed aesthetic services and health coaching.

Industry/Entity Type

Spa

Colors
fbee3e
fece3e
eea4c8
e667a6
fbee3d

Requirements
Must have
• Locations in Lakeview and Cedar Point
Phone 407-555-0148
website www.dewandwillow-example.com

Boards for each:
Aesthetic Treatments
Cosmetic Injectables
Quoria facial
add color vs too many earthtones, to catch the eye perhaps using yellow, something that catches the eye and stands out from the normal everyday
Thank you!!!!
Nice to have
• Boards for each:
Aesthetic Treatments
Cosmetic Injectables
Quoria facial
add color vs too many earthtones, to catch the eye
photos that match services,
Thank you!!!!

```html
<!DOCTYPE html>
<html lang="en">
<head>
<meta charset="utf-8">
<title>Dew and Willow – Aesthetic Treatments Billboard</title>
<link rel="stylesheet" href="https://fonts.googleapis.com/css2?family=Cinzel:wght@400;700&family=Montserrat:wght@600;700&display=swap">
<style>
  :root {
    --page-bg: #e6e6ea;
    --board-top: #e9e9ec;
    --board-bottom: #ffffff;
    --headline-pink: #e667a6;
    --band-yellow: #fece3e;
    --ink-dark: #3a3a3c;
    --ink-grey: #4a4a4d;
    --brand-gold: #c8a870;
    --photo-hair: #c79a68;
    --photo-top: #d9d5d2;
    --photo-light: #f6f4f3;
  }
  html, body {
    margin: 0;
    padding: 0;
    width: 1059px;
    height: 1200px;
    overflow: hidden;
    background: var(--page-bg);
  }
  .canvas {
    position: relative;
    width: 1059px;
    height: 1200px;
  }
  .billboard {
    position: absolute;
    left: 29px;
    top: 475px;
    width: 1000px;
    height: 250px;
    background: linear-gradient(180deg, var(--board-top) 0%, var(--board-bottom) 85%);
    overflow: hidden;
    box-shadow: 0 6px 24px rgba(0,0,0,0.12);
  }
  .model-photo {
    position: absolute;
    left: 115px;
    top: 0;
    width: 245px;
    height: 235px;
    background:
      radial-gradient(ellipse 45% 55% at 58% 42%, rgba(199,154,104,0.85) 0%, rgba(199,154,104,0.4) 50%, rgba(246,244,243,0) 80%),
      linear-gradient(180deg, var(--photo-top) 0%, var(--photo-light) 60%, rgba(255,255,255,0) 100%);
  }
  .headline {
    position: absolute;
    left: 374px;
    top: 64px;
    margin: 0;
    font-family: "Cinzel", serif;
    font-weight: 700;
    font-size: 42px;
    line-height: 1;
    letter-spacing: 0.5px;
    color: var(--headline-pink);
    white-space: nowrap;
  }
  .locations {
    position: absolute;
    left: 374px;
    top: 124px;
    width: 301px;
    height: 25px;
    background: var(--band-yellow);
    font-family: "Montserrat", sans-serif;
    font-weight: 600;
    font-size: 14px;
    line-height: 25px;
    color: var(--ink-dark);
    padding-left: 14px;
    box-sizing: border-box;
    letter-spacing: 0.2px;
    white-space: nowrap;
  }
  .contact {
    position: absolute;
    left: 374px;
    top: 168px;
    font-family: "Montserrat", sans-serif;
    font-weight: 600;
    color: var(--ink-grey);
  }
  .contact .phone {
    display: block;
    font-size: 24px;
    line-height: 28px;
  }
  .contact .website {
    display: block;
    font-size: 11.5px;
    line-height: 16px;
    letter-spacing: 0.3px;
  }
  .brand {
    position: absolute;
    left: 736px;
    top: 178px;
    display: flex;
    align-items: center;
    gap: 12px;
  }
  .brand-dot {
    width: 40px;
    height: 40px;
    border-radius: 50%;
    background: var(--brand-gold);
    flex: none;
  }
  .brand-name {
    font-family: "Cinzel", serif;
    font-weight: 400;
    font-size: 16px;
    line-height: 20px;
    letter-spacing: 1px;
    color: var(--brand-gold);
    width: 220px;
  }
</style>
</head>
<body>
  <main class="canvas">
    <section class="billboard" aria-label="Aesthetic Treatments billboard">
      <div class="model-photo" role="img" aria-label="Photo of a woman with long flowing golden hair in a white top"></div>
      <h1 class="headline">Aesthetic Treatments</h1>
      <div class="locations">LAKEVIEW AND CEDAR POINT</div>
      <div class="contact">
        <span class="phone">407-555-0148</span>
        <span class="website">WWW.DEWANDWILLOW-EXAMPLE.COM</span>
      </div>
      <div class="brand">
        <span class="brand-dot" aria-hidden="true"></span>
        <span class="brand-name">Marigold Radiance<br>Med Spa</span>
      </div>
    </section>
  </main>
</body>
</html>
```